Drag Show Flyer

We are holding a Drag Show, we are looking for something fun and exciting, over the top is a must.

Show Date: Saturday September 2nd 2017
Venue: Pebble Lantern Cafe Bunbury
Doors open 7pm
Tickets: $50 per person, includes glass of sparkling on arrival and canapes
Tickets available at the Venue or from ticketmoor.com.au

Target Market(s)

Female, Hens Party, LBGT

Industry/Entity Type

Entertainment

Colors

Designer to choose colors to be used in the design.

Requirements
Must have
• Show Date: Saturday September 2nd 2017
• Venue: Pebble Lantern Cafe Bunbury
• Doors open 7pm
• Tickets: $50 per person, includes glass of sparkling on arrival and canapes
• Tickets available at the Venue or from ticketmoor.com.au

```html
<!DOCTYPE html>
<html lang="en">
<head>
<meta charset="utf-8">
<title>Drag Show Flyer</title>
<link href="https://fonts.googleapis.com/css2?family=Russo+One&family=Oswald:wght@500;600&family=Arimo:ital,wght@0,400;0,700;1,400&display=swap" rel="stylesheet">
<style>
  :root{
    --stage:#a7a8ab;
    --white:#ffffff;
    --pink:#e4157f;
    --yellow:#fff200;
    --ink:#1a1a1a;
    --night:#0a0614;
  }
  html,body{margin:0;width:1200px;height:1182px;overflow:hidden;background:var(--stage);}
  .flyer{position:absolute;left:274px;top:105px;width:662px;height:935px;box-shadow:0 6px 24px rgba(0,0,0,.25);}
  .flyer svg{display:block;width:100%;height:100%;}
  .headline{font-family:"Russo One",sans-serif;fill:var(--white);}
  .day{font-family:"Oswald",sans-serif;font-weight:600;fill:var(--yellow);}
  .date{font-family:"Oswald",sans-serif;font-weight:500;fill:var(--ink);}
  .venue{font-family:"Arimo",Arial,sans-serif;font-weight:700;fill:var(--white);}
  .doors{font-family:"Arimo",Arial,sans-serif;font-weight:700;fill:var(--pink);}
  .ticket-label{font-family:"Oswald",sans-serif;font-weight:500;fill:var(--ink);}
  .ticket-price{font-family:"Oswald",sans-serif;font-weight:500;fill:var(--pink);}
  .ticket-note{font-family:"Arimo",Arial,sans-serif;fill:var(--ink);}
  .availability{font-family:"Arimo",Arial,sans-serif;font-style:italic;fill:var(--ink);}
  .availability .link{fill:var(--pink);}
  .partner{font-family:"Arimo",Arial,sans-serif;font-weight:700;fill:var(--ink);}
</style>
</head>
<body>
<div class="flyer">
<svg viewBox="0 0 799 1130" xmlns="http://www.w3.org/2000/svg">
  <defs>
    <linearGradient id="lightsGrad" x1="0" y1="0" x2="1" y2="1">
      <stop offset="0" stop-color="#2a1060"/>
      <stop offset=".35" stop-color="#6a1fc8"/>
      <stop offset=".7" stop-color="#2a6fe0"/>
      <stop offset="1" stop-color="#34d2da"/>
    </linearGradient>
    <linearGradient id="photoGrad" x1="0" y1="0" x2="1" y2="1">
      <stop offset="0" stop-color="#2a5fd0"/>
      <stop offset=".3" stop-color="#c8305a"/>
      <stop offset=".55" stop-color="#7a4a3a"/>
      <stop offset=".8" stop-color="#3a2a30"/>
      <stop offset="1" stop-color="#1a1424"/>
    </linearGradient>
    <linearGradient id="photoFade" x1="0" y1="0" x2="0" y2="1">
      <stop offset=".6" stop-color="#0a0614" stop-opacity="0"/>
      <stop offset="1" stop-color="#0a0614" stop-opacity=".9"/>
    </linearGradient>
    <filter id="pinkGlow" x="-20%" y="-30%" width="140%" height="160%">
      <feDropShadow dx="0" dy="0" stdDeviation="9" flood-color="#e4157f" flood-opacity=".95"/>
    </filter>
  </defs>

  <!-- club lights backdrop -->
  <rect class="lights" width="799" height="1130" fill="url(#lightsGrad)" role="img" aria-label="Glowing dotted nightclub light pattern in purple, blue and teal"/>

  <!-- party photo -->
  <g class="photo" role="img" aria-label="Photo of women dancing and laughing in a nightclub with flying hair">
    <rect width="799" height="690" fill="url(#photoGrad)"/>
    <rect width="799" height="690" fill="url(#photoFade)"/>
  </g>

  <!-- headline -->
  <g class="headline" filter="url(#pinkGlow)">
    <text x="90" y="575" font-size="128" textLength="600" lengthAdjust="spacingAndGlyphs" transform="rotate(-5.5 90 575)">DRAG</text>
    <text x="95" y="700" font-size="128" textLength="620" lengthAdjust="spacingAndGlyphs" transform="rotate(-5.5 95 700)">SHOW</text>
  </g>

  <!-- date band -->
  <polygon class="date-band" points="101,716 714,655 715,713 104,778" fill="var(--pink)"/>
  <text class="day" x="118" y="770" font-size="72" textLength="238" lengthAdjust="spacingAndGlyphs" transform="rotate(-5.6 118 770)">SATURDAY</text>
  <text class="date" x="372" y="744" font-size="40" textLength="308" lengthAdjust="spacingAndGlyphs" transform="rotate(-5.6 372 744)">SEPTEMBER.2ND.2017</text>

  <!-- venue block -->
  <polygon class="venue-block" points="186,800 610,752 632,760 626,860 640,900 560,950 300,975 180,985 172,940 190,900 176,840" fill="var(--night)"/>
  <text class="venue" x="411" y="840" font-size="25" text-anchor="middle">Venue:</text>
  <text class="venue" x="411" y="867" font-size="25" text-anchor="middle">Pebble Lantern Café Bunbury</text>
  <text class="doors" x="404" y="902" font-size="18" text-anchor="middle">DOORS OPEN 7PM</text>

  <!-- footer -->
  <polygon class="footer" points="0,1085 799,1020 799,1130 0,1130" fill="var(--white)"/>

  <!-- ticket band -->
  <polygon class="ticket-band" points="0,1023 379,983 379,1063 0,1105" fill="var(--yellow)"/>
  <g transform="rotate(-6 27 1068)">
    <text x="27" y="1068"><tspan class="ticket-label" font-size="28">TICKETS: </tspan><tspan class="ticket-price" font-size="42">$50</tspan><tspan class="ticket-label" font-size="28"> PER PERSON</tspan></text>
    <text class="ticket-note" x="29" y="1086" font-size="13.5">includes glass of sparkling on arrival and canapes</text>
  </g>

  <text class="availability" x="117" y="1111" font-size="13">Tickets available at the Venue or from <tspan class="link">ticketmoor.com.au</tspan></text>

  <!-- partners -->
  <text class="partner" x="472" y="1092" font-size="11">Pebble Lantern Cafe</text>
  <circle cx="618" cy="1087" r="23" fill="var(--ink)"/>
  <text class="partner" x="647" y="1084" font-size="11">The Velvet</text>
  <text class="partner" x="647" y="1098" font-size="11">Circle</text>
  <rect class="badge" x="709" y="1060" width="56" height="55" fill="#ece7ea"/>
</svg>
</div>
</body>
</html>
```